uk based ecommerce website requires fresh look ,high quality look and feel

we are a web based company selling eco friendly ground reinforcement grids to diy and construction sectors
our existing website is www.pondermeshpaths.co.uk ,

we have already updated the logo so that is the branding sorted .so we need a ecommerce website that is very much up-to date in design and layout and which has content management system for ease of use so that we can add products and information as required.

Use current logo as reference for colour scheme.
www.pondermeshpaths.co.uk

The current website has 6 pages accessible through the navigation bar, I would now like 5 pages, removing the need for the Trade Enquiries page possibly have it with along with contact us.

Target Market(s)

construction industry , diy end users,
retail market, landscapers, gardeners

Industry/Entity Type

Construction

Font styles to use
Other font styles liked:
• logo font prometo

Colors
f78f20
9bcb3c

Requirements
Must have
• logo colours and logo design in website with cms responsive design for tablet and mobile devices
• expect content to work flawlessly and look great across all devices
• HTML 5 custom design with coding as required
• must have good experiance in ecommerce website design
• eye catching, high quality look and feel and very user friedly ,very up-to date.
Nice to have
• picture slider show
• explain in writing what exactly i am getting in my ecommerce website
Should not have
• plain , basic design , old fashion looking ,cheap look

```html
<!DOCTYPE html>
<html lang="en">
<head>
<meta charset="utf-8">
<title>Pondermesh Ground Solutions</title>
<link href="https://fonts.googleapis.com/css2?family=Roboto:wght@400;500;700&family=Roboto+Condensed:wght@700&display=swap" rel="stylesheet">
<style>
:root{
  --orange:#f78f20;
  --orange-dark:#e57e12;
  --green:#9bcb3c;
  --green-dark:#6fa227;
  --ink:#222;
  --muted:#666;
  --panel:#f4f4f4;
  --footer:#1e1e1e;
  --white:#fff;
}
*{box-sizing:border-box;margin:0;padding:0}
html,body{width:1200px;height:2866px;overflow:hidden}
body{font-family:"Roboto",Arial,sans-serif;color:var(--ink);background:var(--white);position:relative}
.abs{position:absolute}
.topbar{left:0;top:0;width:1200px;height:52px;background:linear-gradient(var(--green),var(--green-dark));color:var(--white);font-size:13px;font-weight:500}
.topbar .msg{left:76px;top:19px}
.topbar .phones{right:76px;top:18px;display:flex;align-items:center;gap:10px}
.header{left:0;top:52px;width:1200px;height:101px}
.brand{left:76px;top:28px;display:flex;align-items:center;gap:10px}
.brand .dot{width:44px;height:44px;border-radius:50%;background:var(--green)}
.brand .name{font-weight:700;font-size:20px;line-height:1.05;color:var(--orange)}
.cart{right:76px;top:30px;display:flex;align-items:center;gap:10px;font-size:16px}
.cart small{display:block;color:var(--orange);font-size:14px}
.nav{left:0;top:153px;width:1200px;height:55px;background:linear-gradient(var(--orange),var(--orange-dark));display:flex}
.nav .products{margin-left:73px;width:210px;background:var(--green);color:var(--white);font-weight:700;font-size:16px;display:flex;align-items:center;justify-content:space-between;padding:0 30px}
.nav a{color:var(--white);text-decoration:none;font-size:13px;font-weight:500;display:flex;align-items:center;padding:0 32px;border-right:1px solid rgba(255,255,255,.3)}
.hero{left:0;top:208px;width:1200px;height:501px;background:linear-gradient(100deg,#7a6f5e 0%,#9a928a 30%,#b9b6b0 55%,#8d8c86 80%,#5f6b4a 100%)}
.hero .line{display:block;width:max-content;margin:0 auto 6px;background:rgba(30,30,30,.55);color:var(--white);font-family:"Roboto Condensed",sans-serif;font-size:38px;padding:0 8px;line-height:46px}
.hero .caption{left:0;top:228px;width:1200px;text-align:center}
.hero .arrow{top:215px;width:44px;height:44px;background:rgba(0,0,0,.35);display:flex;align-items:center;justify-content:center}
.intro{left:0;top:768px;width:1200px;text-align:center}
.intro h1{font-size:25px;font-weight:500}
.intro p{width:820px;margin:18px auto 0;font-size:14px;color:var(--muted);line-height:21px}
.feature{top:889px;width:512px;height:242px;background:var(--panel)}
.feature .pic{left:0;top:0;width:240px;height:242px;clip-path:polygon(0 0,75% 0,100% 50%,75% 100%,0 100%)}
.feature h2{left:252px;top:36px;color:var(--orange);font-size:18px;font-weight:700;line-height:22px}
.feature p{left:252px;top:100px;width:220px;font-size:13px;color:var(--muted);line-height:21px}
.btn{display:inline-flex;align-items:center;justify-content:center;background:var(--orange);color:var(--white);font-size:12px;font-weight:700;border-radius:22px}
.feature .btn{left:252px;top:173px;width:126px;height:36px}
.product{width:245px}
.product .panel{left:0;width:245px;height:325px;background:var(--panel)}
.product .hex{left:19px;top:0;width:208px;height:240px;background:var(--orange);clip-path:polygon(50% 0,100% 25%,100% 75%,50% 100%,0 75%,0 25%)}
.product .hex div{position:absolute;left:5px;top:5px;width:198px;height:230px;clip-path:polygon(50% 0,100% 25%,100% 75%,50% 100%,0 75%,0 25%)}
.product .info{left:0;top:262px;width:245px;text-align:center}
.product h3{color:var(--orange);font-size:15px;font-weight:700}
.product .price{font-size:16px;font-weight:700;margin-top:8px}
.product .detail{font-size:13px;margin-top:8px}
.product .rate{font-size:11px;margin-top:10px;color:var(--ink)}
.product .rate span{color:var(--orange);font-size:13px;letter-spacing:1px;margin-right:8px}
.product .btn{margin-top:14px;width:126px;height:38px}
.more{left:489px;top:2165px;width:222px;height:46px;border-radius:23px;background:#f4f4f4;box-shadow:0 2px 4px rgba(0,0,0,.2);display:flex;align-items:center;justify-content:center;font-size:13px;font-weight:700;color:#777}
.help{left:0;top:2265px;width:1200px;height:277px;background:linear-gradient(135deg,#8cc23a,#6ea629);text-align:center;color:var(--white)}
.help h2{margin-top:70px;font-size:22px;font-weight:700}
.help p{margin-top:10px;font-size:26px;font-weight:500}
.help .cta{display:inline-flex;align-items:center;gap:10px;margin-top:28px;width:176px;height:46px;justify-content:center;border-radius:23px;background:var(--white);color:var(--ink);font-size:13px;font-weight:700}
.footer{left:0;top:2542px;width:1200px;height:267px;background:var(--footer);color:#bbb}
.footer .fbrand{left:76px;top:40px;display:flex;align-items:center;gap:10px}
.footer .fbrand .dot{width:44px;height:44px;border-radius:50%;background:#aaa}
.footer .fbrand .name{color:var(--white);font-weight:700;font-size:18px;line-height:1.05}
.footer .tag{left:76px;top:144px;width:290px;font-size:13px;line-height:20px}
.footer h4{color:var(--white);font-size:16px;font-weight:500}
.footer ul{list-style:none;font-size:13px}
.footer li{display:flex;gap:10px;margin-bottom:14px;line-height:18px;width:210px}
.footer li i{flex:none;width:15px;height:15px;border-radius:50%;background:var(--green);margin-top:2px;position:relative}
.footer li i::after{content:"";position:absolute;left:5px;top:4px;width:4px;height:4px;border-right:2px solid var(--footer);border-top:2px solid var(--footer);transform:rotate(45deg)}
.footer input{display:block;width:205px;height:34px;border:none;border-radius:17px;padding:0 18px;font-size:12px;font-family:inherit;margin-bottom:13px}
.footer .submit{left:88px;top:148px;width:117px;height:33px;border-radius:17px;background:var(--green);color:var(--white);font-size:13px;font-weight:700}
.bottom{left:0;top:2809px;width:1200px;height:57px;background:#f7f7f7;font-size:12px}
.bottom .copy{left:76px;top:21px}
.bottom .copy b{color:var(--green)}
.cards{right:76px;top:16px;display:flex;gap:6px}
.cards div{width:38px;height:24px;border-radius:3px;background:#c9d2e0}
</style>
</head>
<body>

<div class="abs topbar">
  <div class="abs msg">24 HOUR MESSAGING SERVICE</div>
  <div class="abs phones">
    <svg width="18" height="14" viewBox="0 0 18 14"><path d="M1 4c0-2 3-3 8-3s8 1 8 3v2h-4V4H5v2H1z M4 7h10l2 6H2z" fill="#fff"/></svg>
    <span>Call Us &nbsp;0139-555-0182 , &nbsp;&nbsp;0845-555-0146</span>
  </div>
</div>

<header class="abs header">
  <div class="abs brand"><div class="dot"></div><div class="name">PONDERMESH<br><span style="font-size:13px">GROUND SOLUTIONS</span></div></div>
  <div class="abs cart">
    <svg width="40" height="36" viewBox="0 0 40 36"><path d="M2 12h36l-5 18H7z" fill="none" stroke="#222" stroke-width="3"/><path d="M12 12 20 2l8 10" fill="none" stroke="#222" stroke-width="3"/><path d="M13 17v8M20 17v8M27 17v8" stroke="#222" stroke-width="2.5"/></svg>
    <div>Shopping Cart<small>(0)Item</small></div>
  </div>
</header>

<nav class="abs nav">
  <div class="products">PRODUCTS <span>›</span></div>
  <a>SHOP</a><a>ABOUT US</a><a>GROUND SOLUTIONS</a><a>CELL</a><a>GRAVEL</a><a>CONTACT US</a>
</nav>

<section class="abs hero" role="img" aria-label="Gravel path laid on a hexagonal reinforcement grid beside a brick edging">
  <div class="abs arrow" style="left:0"><svg width="14" height="22"><path d="M11 2 3 11l8 9" stroke="#fff" stroke-width="3" fill="none"/></svg></div>
  <div class="abs arrow" style="right:0"><svg width="14" height="22"><path d="M3 2l8 9-8 9" stroke="#fff" stroke-width="3" fill="none"/></svg></div>
  <div class="abs caption"><span class="line">PATHGRID MAKES WALKING</span><span class="line">ON IT EASY</span></div>
</section>

<section class="abs intro">
  <h1>PONDERMESH ECO SOLUTIONS LTD</h1>
  <p>Stabilised Gravel Paving grids combines purpose designed Cellular reinforcement Pavers with the natural appearance, strength, security and free draining characteristics of a loose aggregate surface</p>
</section>

<article class="abs feature" style="left:73px">
  <div class="abs pic" role="img" aria-label="Gravel driveway over black hexagon grid" style="background:linear-gradient(#b8b5ae,#4a4a4a)"></div>
  <h2 class="abs">LIGHT DOMESTIC<br>DRIVEWAYS</h2>
  <p class="abs">Neque porro quisquam est qui sit dolorem ipsum quia dolor sit amet, consectetur, adipisci velit</p>
  <span class="abs btn">LEARN MORE</span>
</article>
<article class="abs feature" style="left:615px">
  <div class="abs pic" role="img" aria-label="Grass growing through reinforcement mesh" style="background:linear-gradient(#3c3c3a,#6d8a3c)"></div>
  <h2 class="abs">GRASS REINFORCEMENT<br>MESH AND TURF</h2>
  <p class="abs">Neque porro quisquam est qui sit dolorem ipsum quia dolor sit amet, consectetur, adipisci velit</p>
  <span class="abs btn">LEARN MORE</span>
</article>

<!-- product row one -->
<div class="abs product" style="left:73px;top:1185px"><div class="abs panel" style="top:115px"></div><div class="abs hex"><div role="img" aria-label="Orange honeycomb paving grid close up" style="background:linear-gradient(#d7892e,#b86d1a)"></div></div><div class="abs info"><h3>MESHGRID 40 PAVING</h3><div class="price">£ 44.99</div><div class="detail">View Full Details</div><div class="rate"><span>★★★★☆</span>120 Reviews</div><span class="btn">ADD TO CART</span></div></div>
<div class="abs product" style="left:344px;top:1185px"><div class="abs panel" style="top:115px"></div><div class="abs hex"><div role="img" aria-label="Black grid strip laid next to gravel" style="background:linear-gradient(#9c9c98,#2c2c2c)"></div></div><div class="abs info"><h3>MESHGRID 40 PAVING</h3><div class="price">£ 44.99</div><div class="detail">View Full Details</div><div class="rate"><span>★★★★☆</span>120 Reviews</div><span class="btn">ADD TO CART</span></div></div>
<div class="abs product" style="left:615px;top:1185px"><div class="abs panel" style="top:115px"></div><div class="abs hex"><div role="img" aria-label="Wheeled bin on white grid over gravel" style="background:linear-gradient(#8a8275,#d9dadd)"></div></div><div class="abs info"><h3>MESHGRID 40 PAVING</h3><div class="price">£ 44.99</div><div class="detail">View Full Details</div><div class="rate"><span>★★★★☆</span>120 Reviews</div><span class="btn">ADD TO CART</span></div></div>
<div class="abs product" style="left:885px;top:1185px"><div class="abs panel" style="top:115px"></div><div class="abs hex"><div role="img" aria-label="Tyre on gravel filled grid" style="background:linear-gradient(#5a5a58,#a5a39d)"></div></div><div class="abs info"><h3>MESHGRID 40 PAVING</h3><div class="price">£ 44.99</div><div class="detail">View Full Details</div><div class="rate"><span>★★★★☆</span>120 Reviews</div><span class="btn">ADD TO CART</span></div></div>

<!-- product row two -->
<div class="abs product" style="left:73px;top:1686px"><div class="abs panel" style="top:114px"></div><div class="abs hex"><div role="img" aria-label="House with gravel driveway" style="background:linear-gradient(#a9c7dc,#d7d2c6 55%,#a9a59a)"></div></div><div class="abs info"><h3>MESHGRID 40 PAVING</h3><div class="price">£ 44.99</div><div class="detail">View Full Details</div><div class="rate"><span>★★★★☆</span>120 Reviews</div><span class="btn">ADD TO CART</span></div></div>
<div class="abs product" style="left:344px;top:1686px"><div class="abs panel" style="top:114px"></div><div class="abs hex"><div role="img" aria-label="Dark stones in hexagon cells" style="background:linear-gradient(#4e4a44,#2a2826)"></div></div><div class="abs info"><h3>MESHGRID 40 PAVING</h3><div class="price">£ 44.99</div><div class="detail">View Full Details</div><div class="rate"><span>★★★★☆</span>120 Reviews</div><span class="btn">ADD TO CART</span></div></div>
<div class="abs product" style="left:615px;top:1686px"><div class="abs panel" style="top:114px"></div><div class="abs hex"><div role="img" aria-label="Vehicle tyre on ground grid" style="background:linear-gradient(#6b6a66,#a8a08f)"></div></div><div class="abs info"><h3>MESHGRID 40 PAVING</h3><div class="price">£ 44.99</div><div class="detail">View Full Details</div><div class="rate"><span>★★★★☆</span>120 Reviews</div><span class="btn">ADD TO CART</span></div></div>
<div class="abs product" style="left:885px;top:1686px"><div class="abs panel" style="top:114px"></div><div class="abs hex"><div role="img" aria-label="Installer laying grid panels on sand" style="background:linear-gradient(#d6c3a3,#3a3a3a)"></div></div><div class="abs info"><h3>MESHGRID 40 PAVING</h3><div class="price">£ 44.99</div><div class="detail">View Full Details</div><div class="rate"><span>★★★★☆</span>120 Reviews</div><span class="btn">ADD TO CART</span></div></div>

<div class="abs more">VIEW MORE PRODUCTS</div>

<section class="abs help">
  <h2>NEED HELP / ADVICE OR WANT A QUOTE?</h2>
  <p>CALL US ON: &nbsp;0139-555-0182, &nbsp;0845-555-0146</p>
  <span class="cta"><svg width="14" height="11" viewBox="0 0 14 11"><rect width="14" height="11" fill="#6ea629"/><path d="M0 0l7 6 7-6" stroke="#fff" stroke-width="1.5" fill="none"/></svg>GET IN TOUCH</span>
</section>

<footer class="abs footer">
  <div class="abs fbrand"><div class="dot"></div><div class="name">PONDERMESH<br><span style="font-size:12px">GROUND SOLUTIONS</span></div></div>
  <p class="abs tag">Ground Reinforcement Grids Systems For Ground Stabilisation.</p>
  <div class="abs" style="left:401px;top:48px">
    <h4>LINKS</h4>
    <ul style="margin-top:26px">
      <li><i></i>UK Suppliers Of Ground Reinforcement Systems</li>
      <li><i></i>Gravel Reinforcement Systems</li>
      <li><i></i>Grass Reinforcement Systems</li>
    </ul>
  </div>
  <ul class="abs" style="left:682px;top:94px">
    <li><i></i>Site Map Email</li>
    <li><i></i>Terms of Service</li>
    <li><i></i>Delivery and Returns</li>
  </ul>
  <div class="abs" style="left:921px;top:48px;width:205px">
    <h4 style="margin-left:2px">NEWSLETTER</h4>
    <div style="position:relative;margin-top:24px">
      <input type="text" placeholder="Enter Name">
      <input type="email" placeholder="Enter Email">
      <span class="abs btn submit" style="top:95px">SUBMIT</span>
    </div>
  </div>
</footer>

<div class="abs bottom">
  <div class="abs copy">© 2016 &nbsp;<b>PONDERMESH</b> ECO SOLUTIONS LTD</div>
  <div class="abs cards"><div></div><div style="background:#e6c6a8"></div><div></div><div style="background:#d9e2ee"></div></div>
</div>

</body>
</html>
```